New career and executive coaching business needs a business card design including logo

Company name: 'Bramblefield Growth Partners.' The aim of my coaching engagements is to help people improve their communication in the workplace and achieve their career goals. The process involves working with individuals to help them uncover their strengths and talents, then leverage those to improve their working lives. The Tarwick Inventory is the starting point to the process. I am after an exciting and interesting business card design (including logo)which is professional yet will still get people's attention.

Industry/Entity Type

Business

Contact Information for Business Card

Name: Malcolm Dervaney
Position: Owner
Address: 58 Quorrin Ct, Elmbridge Vic 3190
Phone: 0418923047
Website: bramblefieldgrowth.com.au
Email: malcolm@bgp.com.au

Colors
33a6d7
00a990
0355a3
3176b5

Requirements
Must have
• logo

```html
<!DOCTYPE html>
<html lang="en">
<head>
<meta charset="UTF-8">
<title>Bramblefield Growth Partners — Business Card</title>
<link rel="stylesheet" href="https://fonts.googleapis.com/css2?family=Open+Sans:wght@400;600;700&display=swap">
<style>
  :root {
    --backdrop: #3b3531;
    --card: #0d0d0d;
    --sky: #33a6d7;
    --teal: #00a990;
    --navy: #0355a3;
    --mid-blue: #3176b5;
    --text-light: #e8e8e8;
    --silver: #c9c9c9;
    --rule: #1f5f56;
  }
  * { box-sizing: border-box; margin: 0; padding: 0; }
  html, body {
    width: 1200px;
    height: 900px;
    overflow: hidden;
    background: var(--backdrop);
    font-family: "Open Sans", sans-serif;
  }
  .stage {
    position: relative;
    width: 1200px;
    height: 900px;
    display: flex;
    align-items: center;
    justify-content: center;
    gap: 44px;
  }
  .card {
    width: 520px;
    height: 318px;
    background: var(--card);
    position: relative;
    box-shadow: 0 6px 18px rgba(0,0,0,0.45);
  }

  /* Front: contact side */
  .card-front {
    display: flex;
    align-items: center;
  }
  .brand-block {
    width: 255px;
    display: flex;
    flex-direction: column;
    align-items: center;
    gap: 14px;
  }
  .brand-dot {
    width: 150px;
    height: 150px;
    border-radius: 50%;
    background: var(--mid-blue);
  }
  .brand-name-small {
    color: var(--text-light);
    font-size: 13px;
    font-weight: 600;
    letter-spacing: 0.3px;
  }
  .divider {
    width: 1px;
    height: 150px;
    background: var(--rule);
  }
  .contact {
    padding-left: 16px;
    color: var(--text-light);
    font-size: 13px;
    line-height: 1.4;
  }
  .contact-name {
    color: var(--teal);
    font-weight: 700;
    font-size: 15px;
  }
  .contact-role { font-size: 12px; margin-bottom: 12px; }
  .contact-address { margin-bottom: 12px; }
  .contact-line {
    display: flex;
    align-items: center;
    gap: 8px;
  }
  .contact-line svg { width: 11px; height: 11px; flex: none; }

  /* Back: brand side */
  .card-back {
    display: flex;
    align-items: center;
    justify-content: center;
    gap: 22px;
  }
  .back-dot {
    width: 110px;
    height: 110px;
    border-radius: 50%;
    background: var(--silver);
  }
  .back-name {
    color: var(--silver);
    font-size: 22px;
    font-weight: 600;
    line-height: 1.25;
    letter-spacing: 0.5px;
  }
</style>
</head>
<body>
<main class="stage">
  <section class="card card-front">
    <div class="brand-block">
      <div class="brand-dot"></div>
      <span class="brand-name-small">Bramblefield Growth Partners</span>
    </div>
    <div class="divider"></div>
    <div class="contact">
      <p class="contact-name">Malcolm Dervaney</p>
      <p class="contact-role">Owner</p>
      <p class="contact-address">58 Quorrin Ct, Elmbridge<br>Vic 3190</p>
      <p class="contact-line">
        <svg viewBox="0 0 24 24" aria-hidden="true"><path fill="var(--teal)" d="M6.6 10.8a15.1 15.1 0 006.6 6.6l2.2-2.2a1 1 0 011-.25 11.4 11.4 0 003.6.57 1 1 0 011 1V20a1 1 0 01-1 1A17 17 0 013 4a1 1 0 011-1h3.5a1 1 0 011 1c0 1.25.2 2.45.57 3.6a1 1 0 01-.25 1z"/></svg>
        0418923047
      </p>
      <p class="contact-line">
        <svg viewBox="0 0 24 24" aria-hidden="true"><rect x="2" y="5" width="20" height="14" rx="1.5" fill="var(--teal)"/><path d="M3 6l9 7 9-7" fill="none" stroke="var(--card)" stroke-width="1.8"/></svg>
        malcolm@bgp.com.au
      </p>
      <p class="contact-line">
        <svg viewBox="0 0 24 24" aria-hidden="true"><circle cx="12" cy="12" r="10" fill="var(--teal)"/><path d="M2 12h20M12 2c3 3 3 17 0 20M12 2c-3 3-3 17 0 20" fill="none" stroke="var(--card)" stroke-width="1.5"/></svg>
        bramblefieldgrowth.com.au
      </p>
    </div>
  </section>

  <section class="card card-back">
    <div class="back-dot"></div>
    <p class="back-name">Bramblefield<br>Growth Partners</p>
  </section>
</main>
</body>
</html>
```